Velvet Pressings Techno Label Business Card

I'm looking for a very clean business card for my Velvet Pressings music label. The label focusses on techno music. The card should include:

• my name : Tomas Brandt as "Founder & CEO"
• email address: tomas@velvet-pressings.example
• web: www.velvet-pressings.example
• facebook logo + /velvetpress
• twitter logo + /velvetpress
• soundcloud logo + /velvetpressings

Feel free to include your ideas! I'm looking forward to discuss about it.

Tomas

Industry/Entity Type

Business

Contact Information for Business Card

I don't like glossy cards. Prefer matt.

Requirements
Nice to have
• Maybe on one side the complete logo, other side just the icon.
Should not have
• Flashy stuff. Must be clean and business like style.

```html
<!DOCTYPE html>
<html lang="en">
<head>
<meta charset="utf-8">
<title>Velvet Pressings – Business Card</title>
<link rel="stylesheet" href="https://fonts.googleapis.com/css2?family=Ubuntu:wght@400;500;700&family=Open+Sans:wght@400&display=swap">
<style>
  :root {
    --board: #f0f0f0;
    --brand-orange: #e37016;
    --paper: #ffffff;
    --ink-grey: #7d7d7d;
    --ink-dark: #222222;
    --swatch-label: #d81b4a;
    --shadow: rgba(0, 0, 0, 0.22);
  }
  * { margin: 0; padding: 0; box-sizing: border-box; }
  html, body {
    width: 1200px;
    height: 1066px;
    overflow: hidden;
    background: var(--board);
  }
  .board {
    position: relative;
    width: 1200px;
    height: 1066px;
    background: var(--board);
  }
  .card {
    position: absolute;
    width: 650px;
    height: 392px;
    box-shadow: -18px 26px 38px var(--shadow);
  }
  .card--front {
    left: 125px;
    top: 111px;
    background: var(--brand-orange);
  }
  .card--back {
    left: 388px;
    top: 560px;
    background: var(--paper);
  }
  .front-lockup {
    position: absolute;
    left: 64px;
    top: 153px;
    display: flex;
    align-items: center;
    gap: 20px;
  }
  .front-lockup__dot {
    width: 88px;
    height: 88px;
    border: 13px solid var(--paper);
    border-radius: 50%;
  }
  .front-lockup__name {
    font-family: "Ubuntu", sans-serif;
    font-weight: 700;
    font-size: 43px;
    color: var(--paper);
    letter-spacing: -0.3px;
  }
  .back-mark {
    position: absolute;
    left: 68px;
    top: 105px;
    width: 184px;
    height: 184px;
    border: 20px solid var(--brand-orange);
    border-radius: 50%;
    display: flex;
    align-items: center;
    justify-content: center;
    text-align: center;
    font-family: "Ubuntu", sans-serif;
    font-weight: 700;
    font-size: 20px;
    line-height: 1.15;
    color: var(--brand-orange);
  }
  .person {
    position: absolute;
    left: 326px;
    top: 66px;
    font-family: "Ubuntu", sans-serif;
  }
  .person__name {
    font-weight: 700;
    font-size: 22px;
    color: var(--brand-orange);
    letter-spacing: 0.2px;
  }
  .person__role {
    margin-top: 2px;
    font-weight: 400;
    font-size: 13px;
    color: var(--ink-grey);
    letter-spacing: 0.4px;
  }
  .contact-list {
    position: absolute;
    left: 326px;
    top: 186px;
    list-style: none;
    font-family: "Open Sans", sans-serif;
    font-size: 15px;
    color: var(--ink-grey);
  }
  .contact-list li {
    display: flex;
    align-items: center;
    height: 22.6px;
  }
  .contact-list .icon {
    width: 14px;
    height: 14px;
    margin-right: 9px;
    flex: none;
  }
  .icon--square {
    display: inline-block;
    width: 10px !important;
    height: 10px !important;
    margin-left: 2px;
    margin-right: 11px !important;
    border-radius: 2px;
    background: var(--brand-orange);
  }
  .swatch-note {
    position: absolute;
    left: 915px;
    top: 156px;
    font-family: "Open Sans", sans-serif;
    color: var(--ink-dark);
  }
  .swatch-note__name {
    font-size: 25px;
    color: var(--swatch-label);
    margin-bottom: 38px;
  }
  .swatch-note__values {
    font-size: 27px;
    line-height: 30.5px;
  }
</style>
</head>
<body>
<main class="board">

  <section class="card card--front" aria-label="Card front">
    <div class="front-lockup">
      <span class="front-lockup__dot" aria-hidden="true"></span>
      <span class="front-lockup__name">Velvet Pressings</span>
    </div>
  </section>

  <section class="card card--back" aria-label="Card back">
    <div class="back-mark">Velvet<br>Pressings</div>

    <div class="person">
      <p class="person__name">Tomas Brandt</p>
      <p class="person__role">Founder &amp; CEO</p>
    </div>

    <ul class="contact-list">
      <li>
        <svg class="icon" viewBox="0 0 14 14" aria-hidden="true">
          <path d="M3 1 L5.5 3.5 L4.3 5 C5 6.8 7 8.8 9 9.7 L10.5 8.5 L13 11 L11 13 C6 12.5 1.5 8 1 3 Z" fill="#e37016"/>
        </svg>
        +31685550147
      </li>
      <li>
        <svg class="icon" viewBox="0 0 14 14" aria-hidden="true">
          <rect x="1.5" y="3.5" width="11" height="7.5" fill="#e37016"/>
          <path d="M1.5 3.5 L7 8 L12.5 3.5" fill="none" stroke="#fff" stroke-width="1"/>
        </svg>
        tomas@velvet-pressings.example
      </li>
      <li>
        <svg class="icon" viewBox="0 0 14 14" aria-hidden="true">
          <circle cx="7" cy="7" r="5" fill="none" stroke="#e37016" stroke-width="1.4"/>
          <ellipse cx="7" cy="7" rx="2" ry="5" fill="none" stroke="#e37016" stroke-width="1"/>
          <line x1="2" y1="7" x2="12" y2="7" stroke="#e37016" stroke-width="1"/>
        </svg>
        www.velvet-pressings.example
      </li>
      <li><span class="icon icon--square" aria-hidden="true"></span>/velvetpress</li>
      <li><span class="icon icon--square" aria-hidden="true"></span>/velvetpress</li>
      <li><span class="icon icon--square" aria-hidden="true"></span>/velvetpressings</li>
    </ul>
  </section>

  <aside class="swatch-note">
    <p class="swatch-note__name">Oragne</p>
    <p class="swatch-note__values">C:0<br>M:65<br>Y:100<br>K:0</p>
  </aside>

</main>
</body>
</html>
```